Packaging Design for Vanta Prime

We require an outstanding packaging design for our Vanta Prime brand, which offers hydration electrolyte supplements specifically tailored for athletes and sporty individuals.

Benchmark packaging design from quellix competitor attached. The product packaging contains 20 x 20g sticks of the product.

Target Market

Psychographic: Health-conscious, active lifestyle, values quality, functionality and sustainability.

product description 1:
HYDRATION BOOSTER
Refresh, Replenish, Recharge!

product description 2:
PREMIUM ISOTONIC ELECTROLYTE DRINK
Nutritional Expertise Since 1992.

Existing Logo: to add "since 1992"

Appeal to Target Market: Create a design that resonates with both men and women in the 25-55 age group.

Grafik Design: Develop a visually striking design that grabs attention in online retail environments like Brindleport.

Visuals: glass of water (or symbolic) and sticks (powder) just like benchmark brand quellix.

Design Elements
Use colours that are inside the Vanta-Prime Logo, attached.
Product will be available in 3 flavours. Lemon=yellow, Orange=orange, Black Currant=purple

Typography: Utilize strong, clean, and modern fonts. Ensure readability and create a sense of strength, endurance and reliability.

The product will be available in 3 flavours: Lemon, Orange and Johannisbeere

We look forward to seeing your creative ideas and innovative designs for our Vanta Prime brand packaging.

```html
<!DOCTYPE html>
<html lang="en">
<head>
<meta charset="utf-8">
<title>Vanta Prime Hydration Booster – Orange</title>
<link rel="stylesheet" href="https://fonts.googleapis.com/css2?family=Rubik:wght@400;500;700&family=Oswald:wght@300;400;500&display=swap">
<style>
  :root {
    --backdrop: #dedede;
    --brand-blue: #2443a0;
    --accent-red: #ee4527;
    --band-red: #f04a26;
    --band-yellow: #f7d300;
    --logo-yellow: #e6f00f;
    --logo-pink: #d4186b;
    --text-white: #ffffff;
    --flavour-label: #c2401c;
  }
  html, body {
    margin: 0;
    padding: 0;
    width: 1200px;
    height: 1200px;
    overflow: hidden;
    background: var(--backdrop);
  }
  .canvas { display: block; width: 1200px; height: 1200px; }
  .pouch-blue { fill: var(--brand-blue); }
  .pouch-orange { fill: url(#orangeGradient); }
  .band-yellow { fill: var(--band-yellow); }
  .band-red { fill: var(--band-red); }
  .seal-line { stroke: #111a40; stroke-width: 1.5; stroke-dasharray: 6 4; fill: none; }
  .brand-name { font-family: "Rubik", sans-serif; font-weight: 700; fill: var(--logo-yellow); }
  .brand-dot { fill: var(--logo-pink); }
  .brand-since { font-family: "Rubik", sans-serif; font-weight: 400; fill: var(--text-white); }
  .count-badge { fill: var(--accent-red); }
  .count-number { font-family: "Oswald", sans-serif; font-weight: 500; fill: var(--text-white); }
  .count-label { font-family: "Rubik", sans-serif; font-weight: 500; fill: var(--text-white); }
  .pack-info { font-family: "Oswald", sans-serif; fill: var(--text-white); }
  .pack-info.strong { font-weight: 400; }
  .pack-info.light { font-weight: 300; }
  .icon-line { fill: none; stroke: var(--text-white); stroke-width: 2.5; stroke-linecap: round; stroke-linejoin: round; }
  .icon-fill { fill: var(--text-white); }
  .product-title { font-family: "Rubik", sans-serif; font-weight: 700; fill: var(--text-white); }
  .product-tagline { font-family: "Rubik", sans-serif; font-weight: 500; fill: var(--text-white); }
  .product-type { font-family: "Rubik", sans-serif; font-weight: 700; fill: var(--accent-red); }
  .feature-frame { fill: none; stroke: var(--accent-red); stroke-width: 2; }
  .feature-big { font-family: "Rubik", sans-serif; font-weight: 700; fill: var(--accent-red); }
  .feature-text { font-family: "Oswald", sans-serif; font-weight: 400; fill: var(--accent-red); }
  .feature-icon { fill: none; stroke: var(--accent-red); stroke-width: 2.5; stroke-linecap: round; stroke-linejoin: round; }
  .feature-bolt { fill: var(--accent-red); }
  .flavour-photo { fill: url(#fruitGradient); }
  .flavour-label { font-family: "Rubik", sans-serif; font-weight: 700; fill: var(--flavour-label); }
  .footer-text { font-family: "Oswald", sans-serif; fill: var(--text-white); }
  .footer-text.strong { font-weight: 400; }
  .footer-text.light { font-weight: 300; }
</style>
</head>
<body>
<svg class="canvas" viewBox="0 0 1200 1200" xmlns="http://www.w3.org/2000/svg">
  <defs>
    <linearGradient id="orangeGradient" x1="0" y1="0" x2="1" y2="1">
      <stop offset="0" stop-color="#fbac2c"/>
      <stop offset="1" stop-color="#f3951f"/>
    </linearGradient>
    <radialGradient id="fruitGradient" cx="0.55" cy="0.5" r="0.6">
      <stop offset="0" stop-color="#fbbf45"/>
      <stop offset="0.75" stop-color="#f6a625" stop-opacity="0.7"/>
      <stop offset="1" stop-color="#f59c22" stop-opacity="0"/>
    </radialGradient>
    <clipPath id="pouchShape">
      <path d="M218 146 H974 V1046 Q974 1056 964 1056 H228 Q218 1056 218 1046 Z"/>
    </clipPath>
  </defs>

  <g class="pouch" clip-path="url(#pouchShape)">
    <rect class="pouch-orange" x="218" y="146" width="756" height="910"/>
    <polygon class="pouch-blue" points="218,146 974,146 974,345 218,521"/>
    <line class="seal-line" x1="218" y1="212" x2="974" y2="212"/>

    <!-- brand -->
    <g class="brand">
      <circle class="brand-dot" cx="420" cy="332" r="22"/>
      <text class="brand-name" x="456" y="352" font-size="62" textLength="320" lengthAdjust="spacingAndGlyphs">Vanta Prime</text>
      <text class="brand-since" x="708" y="386" font-size="16" transform="rotate(-13 708 386)">Since 1992</text>
    </g>

    <!-- stick count -->
    <g class="stick-count">
      <rect class="count-badge" x="833" y="371" width="78" height="128" rx="3"/>
      <text class="count-number" x="872" y="455" font-size="72" text-anchor="middle" textLength="64" lengthAdjust="spacingAndGlyphs">20</text>
      <text class="count-label" x="872" y="486" font-size="17" text-anchor="middle">STICKS</text>
    </g>
    <g class="pour-icon">
      <rect class="icon-line" x="783" y="405" width="11" height="42" transform="rotate(45 788 426)"/>
      <circle class="icon-fill" cx="785" cy="436" r="1.3"/>
      <circle class="icon-fill" cx="789" cy="441" r="1.3"/>
      <circle class="icon-fill" cx="783" cy="444" r="1.3"/>
      <path class="icon-line" d="M770 452 H804 L799 498 H775 Z"/>
      <path class="icon-fill" d="M773 472 H801 L799 498 H775 Z"/>
    </g>
    <text class="pack-info strong" x="757" y="474" font-size="26" text-anchor="end">20g x 20</text>
    <text class="pack-info light" x="757" y="498" font-size="19" text-anchor="end">NET WT 0.7oz / 20g</text>

    <!-- product copy -->
    <text class="product-title" x="281" y="607" font-size="58" textLength="627" lengthAdjust="spacingAndGlyphs">HYDRATION BOOSTER</text>
    <text class="product-tagline" x="282" y="655" font-size="26" textLength="443" lengthAdjust="spacingAndGlyphs">REFRESH, REPLENISH &amp; RECHARGE!</text>
    <text class="product-type" x="284" y="713" font-size="27" textLength="567" lengthAdjust="spacingAndGlyphs">PREMIUM ISOTONIC ELECTROLYTE DRINK</text>

    <!-- features -->
    <g class="features">
      <path class="feature-frame" d="M302 752 L639 762 Q652 762 652 775 L651 928 Q651 941 638 941 L303 935 Q290 935 290 922 L289 765 Q289 752 302 752 Z"/>
      <text class="feature-big" x="309" y="823" font-size="42" textLength="50" lengthAdjust="spacingAndGlyphs">5X</text>
      <text class="feature-text" x="368" y="822" font-size="24" textLength="95" lengthAdjust="spacingAndGlyphs">ELECTROLYTES</text>

      <g class="capsule-icon">
        <rect class="feature-icon" x="483" y="778" width="18" height="30" rx="9" transform="rotate(-35 492 793)"/>
        <rect class="feature-icon" x="483" y="810" width="18" height="30" rx="9" transform="rotate(35 492 825)"/>
        <circle class="feature-icon" cx="517" cy="803" r="5"/>
        <circle class="feature-icon" cx="511" cy="818" r="3"/>
      </g>
      <text class="feature-text" x="539" y="810" font-size="24" textLength="72" lengthAdjust="spacingAndGlyphs">VITAMINS</text>
      <text class="feature-text" x="539" y="837" font-size="24" textLength="90" lengthAdjust="spacingAndGlyphs">&amp; MINERALS</text>

      <path class="feature-bolt" d="M344 849 L323 886 H338 L324 912 L356 870 H341 L352 849 Z"/>
      <text class="feature-text" x="368" y="879" font-size="24" textLength="33" lengthAdjust="spacingAndGlyphs">FAST</text>
      <text class="feature-text" x="368" y="906" font-size="24" textLength="79" lengthAdjust="spacingAndGlyphs">HYDRATION</text>

      <g class="dna-icon">
        <path class="feature-icon" d="M474 915 C490 905 492 880 508 872 C516 868 522 866 524 860"/>
        <path class="feature-icon" d="M478 919 C494 912 500 890 514 880 C520 876 526 874 527 866"/>
        <line class="feature-icon" x1="486" y1="905" x2="493" y2="911"/>
        <line class="feature-icon" x1="494" y1="893" x2="501" y2="898"/>
        <line class="feature-icon" x1="502" y1="880" x2="510" y2="884"/>
      </g>
      <text class="feature-text" x="540" y="902" font-size="24" textLength="68" lengthAdjust="spacingAndGlyphs">NON GMO</text>
    </g>

    <!-- flavour imagery area -->
    <rect class="flavour-photo" x="662" y="776" width="268" height="160" rx="60" role="img" aria-label="Photo of whole and halved oranges with green leaves"/>

    <!-- bottom bands -->
    <path class="band-yellow" d="M218 955 L680 962 Q700 962 712 950 L730 935 Q742 926 760 926 H974 V990 H218 Z"/>
    <text class="flavour-label" x="881" y="968" font-size="22" text-anchor="end">ORANGE</text>
    <path class="band-red" d="M218 971 L974 978 V1056 H218 Z"/>
    <text class="footer-text strong" x="300" y="1030" font-size="26" textLength="158" lengthAdjust="spacingAndGlyphs">NET WT 14.1oz / 400g</text>
    <text class="footer-text light" x="902" y="1030" font-size="26" text-anchor="end" textLength="270" lengthAdjust="spacingAndGlyphs">NUTRITIONAL EXPERTISE SINCE 1992</text>
  </g>
</svg>
</body>
</html>
```